Bramble firearms training and consulting

Business card for a new firearms training company. I train persons on firearms safety, personal protection, shooting tactics and CHL.Im a Prior State trooper. I also served 4 years in IRaq as a Protection contractor with the Dept of State. Real world training for Real world situations. I would like the company name to be, BRAMBLE FIREARMS TRAINING AND CONSULTING. Im native american also. Ive provided pics. Put the name Bramble above the arrowhead but rotate the arrowhead to the right with it pointing right. Then place bramble inside the arrowhead. lets see both.
Industry/Entity Type
Business
Contact Information for Business Card
Christian Chatellier817-240-0488shadowtraining33@gmail.com

```html
<!DOCTYPE html>
<html lang="en">
<head>
<meta charset="utf-8">
<title>Bramble Firearms Training and Consulting – Business Card</title>
<link rel="stylesheet" href="https://fonts.googleapis.com/css2?family=Delius&display=swap">
<style>
  :root {
    --backdrop: #141414;
    --card: #f6f6f4;
    --brand-red: #7a1409;
    --accent-red: #9c4a3c;
    --ink: #222222;
  }
  html, body {
    margin: 0;
    padding: 0;
    width: 1200px;
    height: 1147px;
    overflow: hidden;
    background: var(--backdrop);
  }
  .canvas {
    position: relative;
    width: 1200px;
    height: 1147px;
  }
  .card {
    position: absolute;
    left: 265px;
    top: 17px;
    width: 680px;
    height: 1116px;
    background: var(--card);
    font-family: "Delius", cursive;
    color: var(--ink);
  }
  .band,
  .band-rule {
    position: absolute;
    left: 177px;
    width: 326px;
    background: var(--brand-red);
  }
  .band--top { top: 4px; height: 42px; }
  .band-rule--top { top: 52px; height: 3px; }
  .band-rule--bottom { top: 1057px; height: 3px; }
  .band--bottom { top: 1065px; height: 51px; }

  .person {
    position: absolute;
    top: 116px;
    left: 0;
    width: 100%;
    text-align: center;
  }
  .person__name {
    margin: 0;
    font-size: 42px;
    font-weight: 400;
    line-height: 1.1;
    white-space: nowrap;
  }
  .person__role {
    margin: 2px 0 0;
    font-size: 22px;
    line-height: 1.2;
    white-space: nowrap;
  }

  .brand {
    position: absolute;
    top: 466px;
    left: 0;
    width: 100%;
    text-align: center;
  }
  .brand__name {
    display: inline-flex;
    align-items: center;
    gap: 16px;
    font-size: 70px;
    line-height: 1;
    color: var(--brand-red);
    letter-spacing: 2px;
    white-space: nowrap;
  }
  .brand__dot {
    width: 24px;
    height: 24px;
    border-radius: 50%;
    background: var(--brand-red);
  }
  .brand__tagline {
    position: absolute;
    top: 632px;
    left: 0;
    width: 100%;
    margin: 0;
    text-align: center;
    font-size: 26px;
    color: var(--accent-red);
    letter-spacing: 0.5px;
    white-space: nowrap;
  }

  .contact {
    position: absolute;
    top: 892px;
    left: 0;
    width: 100%;
    margin: 0;
    padding: 0;
    list-style: none;
    font-size: 27px;
    line-height: 1;
  }
  .contact__item {
    display: flex;
    justify-content: center;
    align-items: center;
    gap: 14px;
    height: 42px;
    white-space: nowrap;
  }
  .contact__icon { width: 30px; height: 30px; flex: none; }
</style>
</head>
<body>
<div class="canvas">
  <section class="card" aria-label="Business card">
    <div class="band band--top"></div>
    <div class="band-rule band-rule--top"></div>

    <header class="person">
      <h1 class="person__name">Dorian Pellwick</h1>
      <p class="person__role">Trainer and Consultant</p>
    </header>

    <div class="brand">
      <span class="brand__name"><span class="brand__dot"></span>BRAMBLE</span>
    </div>
    <p class="brand__tagline">FIREARMS TRAINING AND CONSULTING</p>

    <ul class="contact">
      <li class="contact__item">
        <svg class="contact__icon" viewBox="0 0 30 30" aria-hidden="true">
          <circle cx="15" cy="15" r="13" fill="none" stroke="#222" stroke-width="2.5"/>
          <path d="M10 8.5 l3 3 -1.5 2 a9 9 0 0 0 5 5 l2 -1.5 3 3 -2 2.5 c-6 0 -12 -6 -12 -12z" fill="#222"/>
        </svg>
        <span>555-317-9062</span>
      </li>
      <li class="contact__item">
        <svg class="contact__icon" viewBox="0 0 30 30" aria-hidden="true">
          <circle cx="15" cy="15" r="14" fill="#222"/>
          <rect x="7.5" y="10" width="15" height="10" rx="1" fill="#fff"/>
          <path d="M7.5 11 l7.5 5 7.5 -5" fill="none" stroke="#222" stroke-width="1.6"/>
        </svg>
        <span>bramblecourse58@mailvento.com</span>
      </li>
      <li class="contact__item">
        <svg class="contact__icon" viewBox="0 0 30 30" aria-hidden="true">
          <circle cx="15" cy="15" r="14" fill="#222"/>
          <path d="M15 7 l8 7 h-2.5 v8 h-4 v-5 h-3 v5 h-4 v-8 h-2.5z" fill="#fff"/>
        </svg>
        <span>740 Corliss Lane, NY 12706</span>
      </li>
    </ul>

    <div class="band-rule band-rule--bottom"></div>
    <div class="band band--bottom"></div>
  </section>
</div>
</body>
</html>
```